Stationery Design for a fast food resturaunt

We just created our logo, we need nice stationary to go with it. We beed the design to be on white background and black background.

Target Market(s)

Landlords who will lease their retail shops to us. Shopping Mall Management.Real Estate Professionals.

Font styles to use
Sans Serif

```html
<!DOCTYPE html>
<html lang="en">
<head>
<meta charset="utf-8">
<title>Northway Kitchen – Business Cards</title>
<link href="https://fonts.googleapis.com/css2?family=Open+Sans:wght@400;600&display=swap" rel="stylesheet">
<style>
  :root {
    --backdrop: #e6e6e6;
    --charcoal: #2b2b2b;
    --paper: #f3f3f3;
    --amber: #e8ac0a;
    --ink: #222222;
    --light: #f5f5f5;
  }
  * { margin: 0; padding: 0; box-sizing: border-box; }
  html, body {
    width: 1200px; height: 900px; overflow: hidden;
    background: var(--backdrop);
    font-family: "Open Sans", sans-serif;
  }
  .card {
    position: absolute;
    width: 600px; height: 340px;
    box-shadow: 0 6px 18px rgba(0,0,0,0.18);
  }
  .card--dark { left: 110px; top: 100px; background: var(--charcoal); }
  .card--light { left: 490px; top: 470px; background: var(--paper); }

  .brand {
    position: absolute;
    font-weight: 400; font-size: 30px; letter-spacing: 0.5px;
    white-space: nowrap;
  }
  .card--dark .brand { left: 120px; top: 210px; color: var(--light); }
  .card--light .brand { right: 60px; top: 64px; color: var(--ink); }

  .web {
    position: absolute; right: 48px; bottom: 46px;
    font-size: 15px; letter-spacing: 3px; white-space: nowrap;
  }
  .card--dark .web { color: var(--light); }
  .card--light .web { color: var(--ink); }
  .web-bar {
    position: absolute; right: 48px; bottom: 22px;
    width: 190px; height: 14px; background: var(--amber);
  }

  .edge-mark {
    position: absolute; left: 0; top: 118px;
    width: 16px; height: 48px; background: var(--charcoal);
  }
  .person { position: absolute; left: 52px; top: 114px; }
  .person__name { font-size: 22px; font-weight: 600; color: var(--ink); }
  .person__role { font-size: 13px; color: var(--amber); letter-spacing: 0.5px; }

  .address {
    position: absolute; left: 52px; top: 212px;
    font-size: 15px; line-height: 1.35; color: var(--ink); font-style: normal;
  }
  .contact {
    position: absolute; left: 52px; top: 282px;
    list-style: none; font-size: 15px; line-height: 1.35; color: var(--ink);
  }
  .contact li { display: flex; align-items: center; gap: 10px; }
  .contact svg { width: 14px; height: 14px; }
</style>
</head>
<body>
  <section class="card card--dark">
    <div class="brand">Northway Kitchen</div>
    <div class="web">www.northway-kitchen.net</div>
    <div class="web-bar"></div>
  </section>

  <section class="card card--light">
    <div class="brand">Northway Kitchen</div>
    <div class="edge-mark"></div>
    <div class="person">
      <div class="person__name">Daniel Reyes</div>
      <div class="person__role">DIRECTOR</div>
    </div>
    <address class="address">
      Northway Kitchen,<br>
      218 Harbor Point Plaza<br>
      Redmond, WA 98052
    </address>
    <ul class="contact">
      <li>
        <svg viewBox="0 0 16 16" aria-hidden="true"><path d="M4 1.5 L6.5 4.5 L5 6.5 Q6.5 9.5 9.5 11 L11.5 9.5 L14.5 12 L12.5 14.5 Q5 13.5 1.5 3.5 Z" fill="none" stroke="#e8ac0a" stroke-width="1.4" stroke-linejoin="round"/></svg>
        01234 555 210
      </li>
      <li>
        <svg viewBox="0 0 16 16" aria-hidden="true"><rect x="1.5" y="3.5" width="13" height="9" fill="none" stroke="#e8ac0a" stroke-width="1.4"/><path d="M1.5 3.5 L8 9 L14.5 3.5" fill="none" stroke="#e8ac0a" stroke-width="1.4"/></svg>
        dreyes@northway-kitchen.net
      </li>
    </ul>
    <div class="web">www.northway-kitchen.net</div>
    <div class="web-bar"></div>
  </section>
</body>
</html>
```